Website Design for my Copper Distillation Equipment Business Nature Sciencey Theme

I already have a website www.cascobrewworks.com and its a sitevelo website builder one. But I cannot get the design right at all. I need this fixed.

I have logo. I need a redesign, for my website, the home page, that maybe I can have something similar in design- I can use as template to copy, for other pages so the whole thing matches? Look at my website so you understand I have a few pages...but most are links. Its a competition. Code has to be easy for me to implement, I am not expert.

Your advice needed..It would be a plus if I can update this myself throughout time. If I could have this explained to me too, the maintenance of it...how would I do this too..etc..pretend I am a child when you explain, if you can. I am not good with this stuff but I am smart and can learn fast.

I want a high end look. Maybe like an ivy league college-y look too, real preppy, chemistry...science-y, nature like is good, leaves, drops water, fields of wheat, lavender, etc.

I want every page to look similar, but the home page is what I want to be the main showpiece,..and I want each page have a little text section, maybe a photos section and a video section, for that market. Like a nice website. If I am not doing this right, let me know. I can work with you. Just help me, please. Let me know if I am doing this right.

When I pick my winning design, for my website, I will hire the artist one-on-one to re-design my shopping cart next. Or if I need additional help with implementing this current design, I can hire the same artist again too. I have a blog that I may want to hire the redesign as well too, but later on. My point is I am not just looking for one project here but I want to follow up with winning artist. So it would be return business for the winner.

I got my logo done here so I am repeat customer. And I have given that winning artist other design work.

Target Market(s)

Moonshine Stills I sell most, Essential Oil Business, Micro and Craft Distilleries, Canna-businesses, Alcohol Fuel

Industry/Entity Type

Business

Number of Pages Required

5+ page

Colors
ec1f27

Requirements
Must have
• The categories for the stills must be prominent and eye catching. The main photo I would like to be naturelike theme, but you can try out different things with me. I am open to ideas and suggestions. I would like this to be implemented easy and fast.
Nice to have
• My logo in it. You can use any of my photos as well from my pictoshare account. https://www.pictoshare.com/photos/81724596@K09/
• Colors of my Logo...matching design.
• Maybe some basic stock photos you see would match for me..
• Chemistry like symbols for the categories, I love that.

```html
<!DOCTYPE html>
<html lang="en">
<head>
<meta charset="utf-8">
<title>Casco Brew Works – Home</title>
<link href="https://fonts.googleapis.com/css2?family=Questrial&family=Open+Sans:wght@400;600&family=Parisienne&family=Federo&display=swap" rel="stylesheet">
<style>
:root{
  --green-dark:#2f8f14;
  --green-mid:#5fc21e;
  --green-light:#b8ea55;
  --leaf:#7fd62a;
  --maroon:#5a1a14;
  --maroon-deep:#4a1510;
  --tile-red:#7a1d16;
  --arrow-red:#b3241d;
  --ink:#4a4a4a;
  --nav-ink:#2c3a12;
  --white:#ffffff;
  --card-bg:#ececec;
}
*{margin:0;padding:0;box-sizing:border-box}
html,body{width:765px;height:1200px;overflow:hidden;background:var(--white)}
.page{position:relative;width:765px;height:1200px;font-family:"Open Sans",sans-serif}

/* header */
.site-header{position:absolute;left:0;top:0;width:765px;height:257px;
  background:radial-gradient(ellipse at 50% 50%,var(--green-light) 0%,var(--green-mid) 45%,var(--green-dark) 100%)}
.header-foliage{position:absolute;top:0;width:130px;height:70px}
.header-foliage.left{left:60px;background:radial-gradient(ellipse at 50% 0%,rgba(150,230,60,.95) 0%,rgba(110,200,40,.6) 45%,rgba(110,200,40,0) 75%)}
.header-foliage.right{left:580px;background:radial-gradient(ellipse at 50% 0%,rgba(150,230,60,.95) 0%,rgba(110,200,40,.6) 45%,rgba(110,200,40,0) 75%)}
.nav{position:absolute;top:82px;height:20px;border-bottom:1px solid var(--nav-ink);
  font-family:"Questrial",sans-serif;font-size:10px;color:var(--nav-ink);text-transform:uppercase}
.nav span{position:absolute;top:2px;white-space:nowrap}
.nav-left{left:47px;width:278px}
.nav-right{left:441px;width:277px}
.brand{position:absolute;left:332px;top:30px;width:100px;height:90px;display:flex;flex-direction:column;
  align-items:center;justify-content:center;gap:6px}
.brand-dot{width:12px;height:12px;background:var(--maroon)}
.brand-name{font-family:"Questrial",sans-serif;font-size:15px;line-height:17px;color:var(--maroon);text-align:center}
.tagline{position:absolute;left:0;top:136px;width:765px;text-align:center;font-weight:400;
  font-family:"Parisienne",cursive;font-size:21px;color:var(--maroon)}

/* categories */
.categories{position:absolute;left:40px;top:181px;width:685px;height:74px;display:flex}
.category{flex:1;position:relative;border-right:1px solid rgba(255,255,255,.5)}
.category:last-child{border-right:0}
.category-photo{height:49px}
.category-label{height:25px;background:var(--tile-red);color:var(--white);font-size:9.5px;padding:6px 0 0 8px}
.cat-arrow{position:absolute;top:230px;width:10px;height:25px;background:var(--arrow-red)}
.cat-arrow svg{display:block;margin:8px auto 0}

/* hero */
.hero{position:absolute;left:0;top:257px;width:765px;height:339px;
  background:
    radial-gradient(ellipse 150px 110px at 650px 95px,rgba(150,220,50,.95) 0%,rgba(120,200,40,.55) 50%,rgba(120,200,40,0) 100%),
    radial-gradient(ellipse 90px 150px at 90px 180px,rgba(70,70,70,.85) 0%,rgba(70,70,70,0) 100%),
    linear-gradient(180deg,rgba(0,0,0,0) 0%,rgba(0,0,0,0) 48%,#5b4634 56%,#3d2c20 100%),
    linear-gradient(90deg,#5d7a34 0%,#8aa456 30%,#6c8f3a 55%,#9a9a80 80%,#c9c8b6 100%)}
.hero-arrows{position:absolute;left:47px;top:577px;width:38px;height:18px;background:var(--white);display:flex}
.hero-arrows span{flex:1;display:flex;align-items:center;justify-content:center}
.hero-arrows span:first-child{border-right:1px solid #ccc}

/* intro */
.intro-title{position:absolute;left:47px;top:616px;font-family:"Federo",sans-serif;font-weight:400;
  font-size:22px;line-height:25px;color:var(--maroon);font-variant:small-caps;letter-spacing:.3px}
.intro-title .line2{display:block;padding-left:33px}
.intro-text{position:absolute;left:47px;top:680px;width:330px;font-size:8.55px;line-height:15.4px;color:var(--ink)}
.intro-text p{margin-bottom:15.4px}

/* video */
.video-card{position:absolute;left:391px;top:531px;width:327px;height:235px;background:var(--white);padding:7px}
.video-frame{position:relative;width:313px;height:207px;
  background:
    linear-gradient(90deg,rgba(0,0,0,0) 42%,rgba(200,200,210,.85) 45%,rgba(230,230,235,.9) 60%,rgba(0,0,0,0) 63%) 0 0/313px 110px no-repeat,
    radial-gradient(ellipse at 50% 65%,#c07a50 0%,#7a3c22 45%,#2a1a12 100%)}
.play{position:absolute;left:138px;top:92px}
.video-bar{height:14px;background:#1b1b1b;color:#ddd;font-size:6.5px;display:flex;align-items:center;padding:0 6px;gap:8px}
.video-bar .time{margin-left:6px}
.video-bar .right{margin-left:auto;display:flex;gap:7px}
.video-bar i{display:block;width:6px;height:6px;border:1px solid #ddd}

/* product cards */
.product{position:absolute;top:785px;width:155px;height:241px;background:var(--card-bg)}
.product-photo{height:200px}
.buy-btn{position:absolute;left:8px;top:208px;width:139px;height:27px;background:var(--maroon);color:var(--white);
  font-family:"Questrial",sans-serif;font-size:9.5px;text-align:center;line-height:27px}

/* footer */
.site-footer{position:absolute;left:0;top:1075px;width:765px;height:125px;background:var(--maroon-deep);color:var(--white)}
.footer-foliage{position:absolute;left:55px;top:0;width:45px;height:40px;
  background:radial-gradient(ellipse at 50% 20%,rgba(255,255,255,.9) 0%,rgba(255,255,255,.5) 45%,rgba(255,255,255,0) 75%)}
.contact-row{position:absolute;top:25px;font-size:8.5px}
.footer-brand{position:absolute;left:345px;top:14px;width:76px;text-align:center;font-family:"Questrial",sans-serif;font-size:10px;line-height:12px}
.footer-nav{position:absolute;left:0;top:70px;width:765px;text-align:center;font-family:"Questrial",sans-serif;font-size:10px;text-transform:uppercase}
.footer-nav span{margin:0 5px}
.copyright{position:absolute;left:0;top:102px;width:765px;text-align:center;font-size:8.5px}
</style>
</head>
<body>
<div class="page">
  <header class="site-header">
    <div class="header-foliage left" role="img" aria-label="Hanging green leaves"></div>
    <div class="header-foliage right" role="img" aria-label="Hanging green leaves"></div>
    <nav class="nav nav-left">
      <span style="left:15px">Home</span><span style="left:70px">About Us</span>
      <span style="left:139px">Photo Gallery</span><span style="left:236px">Video</span>
    </nav>
    <div class="brand"><div class="brand-dot"></div><div class="brand-name">Casco<br>Brew Works</div></div>
    <nav class="nav nav-right">
      <span style="left:10px">Shop</span><span style="left:61px">Blog</span>
      <span style="left:114px">Books</span><span style="left:172px">Links</span><span style="left:222px">Contact</span>
    </nav>
    <h2 class="tagline">Please Choose the Category of the Still you are looking for...</h2>

    <div class="categories">
      <div class="category"><div class="category-photo" role="img" aria-label="Photo of a copper still on a deck" style="background:linear-gradient(90deg,#e8e6e0 0%,#9fb4c4 35%,#c4b8a8 70%,#7d6a55 100%)"></div><div class="category-label">Stills</div></div>
      <div class="category"><div class="category-photo" role="img" aria-label="Photo of an essential oil distilling workshop" style="background:linear-gradient(90deg,#b8603a 0%,#7a3a22 40%,#c08a6a 70%,#5a2a1a 100%)"></div><div class="category-label">Essential Oils</div></div>
      <div class="category"><div class="category-photo" role="img" aria-label="Photo of alcohol fuel burning in a jar" style="background:radial-gradient(ellipse at 45% 70%,#f2d2a8 0%,#d98a4a 35%,#3a1a10 90%)"></div><div class="category-label">Alcohol Fuel</div></div>
      <div class="category"><div class="category-photo" role="img" aria-label="Photo of a small extraction still" style="background:linear-gradient(90deg,#9a9a5a 0%,#5a5a3a 30%,#2a2a28 55%,#6a7a4a 100%)"></div><div class="category-label">Cannabis</div></div>
      <div class="category"><div class="category-photo" role="img" aria-label="Photo of a stainless steel keg boiler" style="background:linear-gradient(90deg,#6a8a3a 0%,#b8b8a8 35%,#d0d0c8 60%,#6a7a4a 100%)"></div><div class="category-label">Boilers</div></div>
      <div class="category"><div class="category-photo" role="img" aria-label="Photo of a home distiller on grass" style="background:linear-gradient(90deg,#4a7a2a 0%,#7ea04a 40%,#b8b8a8 60%,#4a6a2a 100%)"></div><div class="category-label">Home Distillers</div></div>
      <div class="category"><div class="category-photo" role="img" aria-label="Photo of bucket stills for vodka" style="background:linear-gradient(90deg,#6a7a4a 0%,#e8e8e8 25%,#8a8a7a 50%,#f0f0f0 75%,#6a7a4a 100%)"></div><div class="category-label">Vodka Still</div></div>
    </div>
    <div class="cat-arrow" style="left:30px"><svg width="5" height="9"><path d="M4 0L0 4.5 4 9" fill="none" stroke="#fff" stroke-width="1.5"/></svg></div>
    <div class="cat-arrow" style="left:725px"><svg width="5" height="9"><path d="M1 0l4 4.5L1 9" fill="none" stroke="#fff" stroke-width="1.5"/></svg></div>
  </header>

  <section class="hero" role="img" aria-label="Photo of a countertop copper still with a mason jar on a wooden deck among green leaves"></section>
  <div class="hero-arrows">
    <span><svg width="5" height="9"><path d="M4 0L0 4.5 4 9" fill="none" stroke="#222" stroke-width="1.5"/></svg></span>
    <span><svg width="5" height="9"><path d="M1 0l4 4.5L1 9" fill="none" stroke="#222" stroke-width="1.5"/></svg></span>
  </div>

  <h1 class="intro-title">Purity comes from a<span class="line2">direct connection with Nature...</span></h1>
  <div class="intro-text">
    <p>Welcome to our Website. Are you looking for a Moonshine Still? Are you a Lavender Farm? Are you wanting to distill Essential Oils on your farm and make Hydrosols too? Do you want to make an Herbal Extraction or Tincture? Do you want to start a Home Business? Are you a Micro ( small) Distillery wanting a Set up? Are you a Race Car driver looking for alternative ways to get your Ethanol? Are you a Prepper? Are you interested in Making Alcohol in times of Survival? Do you need clean radiation free Water for your community? Do you want to support Local Farmers, get back to the Source and Nature? Are you a Canna-business or 502?</p>
    <p>My Dream Customer is someone who believes they cannot, but does it anyways and finds out they can! And then they go and teach someone....that is a gift that keeps on giving. Those are the results I want to give. Taking a liquid, turning it into a vapor and then back into a liquid. That is all you need to know.</p>
    <p>To Purchase a Still, you can &nbsp;browse through our Cart. We have How To Articles in our Blog, and in the Links section, also watch step by step Videos and see detailed Photos of all our products. Read our manuals. See our tests results. See me on tv and in magazine articles. I have a weekly Live LiveCast as well, if you want to interact with questions. I can give you projects. We have VoiceLink and MeetRoom.</p>
    <p>Please ask us questions. Call us for a free quote. We sell Distillation Equipment and we can customize your projects. We ship Alcohol Stills all around the world, we are an online only store.</p>
  </div>

  <div class="video-card">
    <div class="video-frame" role="img" aria-label="Video still of a hydrometer floating in a copper pot">
      <svg class="play" width="38" height="38"><circle cx="19" cy="19" r="17" fill="none" stroke="#fff" stroke-width="2"/><path d="M15 11l11 8-11 8z" fill="#fff"/></svg>
    </div>
    <div class="video-bar">
      <svg width="6" height="7"><rect width="2" height="7" fill="#ddd"/><rect x="4" width="2" height="7" fill="#ddd"/></svg>
      <svg width="8" height="7"><path d="M0 0l4 3.5L0 7zM4 0l4 3.5L4 7z" fill="#ddd"/></svg>
      <svg width="8" height="7"><path d="M0 2h2l3-2v7L2 5H0z" fill="#ddd"/></svg>
      <span class="time">0:00 / 2:05:00</span>
      <span class="right"><i></i><i></i><i></i><i></i></span>
    </div>
  </div>

  <div class="product" style="left:391px">
    <div class="product-photo" role="img" aria-label="Photo of a keg still with copper column in a forest" style="background:linear-gradient(90deg,rgba(0,0,0,0) 40%,rgba(190,120,80,.8) 44%,rgba(190,120,80,.8) 50%,rgba(0,0,0,0) 54%) 0 0/155px 120px no-repeat,radial-gradient(ellipse 40px 40px at 50% 80%,#d8d8d8 0%,rgba(200,200,200,0) 100%),linear-gradient(180deg,#8aa05a 0%,#6a7a42 50%,#7aa04a 100%)"></div>
    <div class="buy-btn">BUY A STILL CLICK HERE</div>
  </div>
  <div class="product" style="left:563px">
    <div class="product-photo" role="img" aria-label="Photo of a keg still with copper column on a lawn" style="background:linear-gradient(90deg,rgba(0,0,0,0) 38%,rgba(190,120,80,.8) 41%,rgba(190,120,80,.8) 46%,rgba(0,0,0,0) 49%) 0 0/155px 110px no-repeat,radial-gradient(ellipse 45px 45px at 45% 75%,#d0d0d0 0%,rgba(200,200,200,0) 100%),linear-gradient(180deg,#3a6a2a 0%,#5a8a3a 50%,#7aa84a 100%)"></div>
    <div class="buy-btn">BUY A STILL CLICK HERE</div>
  </div>

  <footer class="site-footer">
    <div class="footer-foliage" role="img" aria-label="White leaf and droplet decoration"></div>
    <div class="contact-row" style="left:270px">+1 555 014 2290</div>
    <div class="footer-brand">Casco<br>Brew Works</div>
    <div class="contact-row" style="left:431px">info@cascobrewworks.com</div>
    <nav class="footer-nav"><span>Home</span><span>About Us</span><span>Photogallery</span><span>Video</span><span>Shop</span><span>Blog</span><span>Books</span><span>Links</span><span>Contact Us</span></nav>
    <div class="copyright">© 2015 Casco Brew Works - All Rights Reserved</div>
  </footer>
</div>
</body>
</html>
```